Mobile App Flyer for Takeaway Tappora

We need a single A4 page flyer to promote our mobile apps for takeaway food solution.

Please visit our web site www.tappora-demo.com and review the retail page for further details but here are a number of the benefits that I'd like to try to include in the flyer.

I do need a catchy title too...

TAKEAWAYS & RESTAURANTS
Tap into the growth market of mobile and online food ordering. With over 51% of UK online ecommerce sales now being conducted on mobiles devices* it’s crucial takeaways and restaurants adopt a suitable mobile strategy.
* Source: QVLD / Brelwick 2016
Stay independent. Go mobile with an online food ordering app that is dedicated and designed specifically for your business. Unlike other solutions, we don’t encourage your customer to use a shared app that then promotes your competitors’ businesses to your customers!
We don’t charge order commission, just a small fixed monthly fee, (pricing published on our web site). As you grow your mobile business you keep all the profits!
Benefit from better Zintaro search results. Did you know Zintaro now favours and ranks businesses with mobile apps higher than those without?
Differentiate your business against other local businesses, create a buzz around your business going “Mobile”!
Free-up your business phone line at peak periods, never miss another order.
Save staff time by accepting unlimited mobile and on-line orders simultaneously, no need to take a call and write the orders down, it also minimises mistakes.
If you buy our Business or Business Plus package we will also provide you an online shop that can be added to your website!
If you’re thinking this isn’t going to be cheap, check our pricing on our web site, you’re going to be very pleasantly surprised.
Attractive interactive menus, show-off your business and food to its best.
Convenience for your customers:
No more holding or busy signal when trying to place an order.
Customer’s order history is saved in the app making re-ordering fast and convenient.
Customers can use convenient online payment providers such as KOINRA, as well as traditional credit cards or of course, cash-on-collection.
Easily and quickly update your menu with seasonal changes, menu items, pricing and even delivery options.
Send promotions to your customers and advise them of seasonal opening times, even message them each time they are close to your business!
Launch an in-app loyalty programme, which rewards your loyal customers and generates repeat business.
There are many reason you should be considering going mobile if. Please call us on 01632 960417 or email us at Info@Tappora-demo.com to discuss your requirements with us.

Target Market(s)

Owners of takeaways and restaurants

Font styles to use
Sans Serif

Colors
33b8a4
3176b5
faa54b

Requirements
Must have
• Tap Pora white and blue logo from website
• Features doc has some screen shots that could be used.
• The format must be reusable for other products so if I develop an app for a golf course, for example, I could use the same layout but change the primary colour of the flyer.
• Doesn't have to be identical to web site but shouldn't be poles apart so that it looks odd!
Nice to have
• At least one picture of a smart phone.

```html
<!DOCTYPE html>
<html lang="en">
<head>
<meta charset="utf-8">
<title>Takeaway Food Retail Solution – Tappora</title>
<link rel="stylesheet" href="https://fonts.googleapis.com/css2?family=Open+Sans:wght@400;600;700&display=swap">
<style>
  :root {
    --accent: #f28a1e;
    --accent-soft: #faa54b;
    --ink: #3c3c3c;
    --muted: #6a6a6a;
    --white: #ffffff;
    --hero-dark: #3a2414;
    --hero-mid: #a8542a;
    --hero-warm: #d9a04a;
  }
  * { box-sizing: border-box; margin: 0; padding: 0; }
  html, body { width: 849px; height: 1200px; overflow: hidden; background: var(--white); }
  body { font-family: "Open Sans", Arial, sans-serif; color: var(--ink); }
  .flyer { position: relative; width: 849px; height: 1200px; overflow: hidden; background: var(--white); }

  .hero-photo {
    position: absolute; left: 0; top: 0; width: 849px; height: 396px;
    background: radial-gradient(ellipse at 35% 55%, var(--hero-warm) 0%, var(--hero-mid) 45%, var(--hero-dark) 100%);
  }
  .phone-photo {
    position: absolute; left: 560px; top: 150px; width: 260px; height: 350px;
    border-radius: 28px;
    background: linear-gradient(160deg, #2d2d2d 0%, #555 40%, #c9a27a 100%);
  }

  .title-band {
    position: absolute; left: 0; top: 396px; width: 425px; height: 48px;
    background: var(--accent); color: var(--white);
    font-weight: 700; font-size: 30px; letter-spacing: 1px;
    padding-left: 85px; line-height: 48px;
  }
  .subtitle {
    position: absolute; left: 85px; top: 460px;
    color: var(--accent); font-weight: 400; font-size: 25px; letter-spacing: 0.5px;
  }

  .benefit-group { position: absolute; }
  .benefit-group .icon { position: absolute; left: 0; top: 2px; width: 26px; height: 26px; }
  .benefit-group ul { list-style: none; margin-left: 36px; }
  .benefit-group li {
    position: relative; font-size: 13.5px; line-height: 19px; padding-left: 12px; margin-bottom: 3px; color: var(--muted);
  }
  .benefit-group li::before {
    content: ""; position: absolute; left: 0; top: 8px; width: 4px; height: 4px; border-radius: 50%; background: var(--muted);
  }
  .group-left-a { left: 50px; top: 540px; width: 370px; }
  .group-left-b { left: 50px; top: 790px; width: 370px; }
  .group-right-a { left: 440px; top: 540px; width: 380px; }
  .group-right-b { left: 440px; top: 745px; width: 380px; }

  .contact-band {
    position: absolute; left: 0; top: 1048px; width: 640px; height: 152px;
    background: var(--accent); color: var(--white);
    padding: 48px 0 0 85px; font-size: 15px; line-height: 22px;
  }
  .brand {
    position: absolute; left: 672px; top: 1100px; display: flex; align-items: center; gap: 8px;
    font-weight: 700; font-size: 30px; color: var(--accent);
  }
  .brand-mark { width: 14px; height: 14px; background: var(--accent); }
</style>
</head>
<body>
<div class="flyer">
  <div class="hero-photo" role="img" aria-label="Close-up photograph of a freshly baked pizza with melted cheese and toppings"></div>
  <div class="phone-photo" role="img" aria-label="Hand holding a smartphone showing the takeaway ordering app"></div>

  <div class="title-band">TAKEAWAY</div>
  <div class="subtitle">FOOD RETAIL SOLUTION</div>

  <section class="benefit-group group-left-a">
    <svg class="icon" viewBox="0 0 26 26" aria-hidden="true"><circle cx="13" cy="13" r="12" fill="var(--accent)"/><path d="M8 13.5l3.5 3.5L18 10" stroke="#fff" stroke-width="2.4" fill="none"/></svg>
    <ul>
      <li>Tap into the growth market of mobile and online food ordering</li>
      <li>Go mobile with an online food ordering app that is dedicated and designed specifically for your business</li>
      <li>Attractive interactive menus, show-off your business and food to its best</li>
      <li>Easily and quickly update your menu with seasonal changes, menu items, pricing and even delivery options</li>
    </ul>
  </section>

  <section class="benefit-group group-left-b">
    <svg class="icon" viewBox="0 0 26 26" aria-hidden="true"><circle cx="13" cy="13" r="12" fill="var(--accent)"/><path d="M9 7h3l1 4-2 1.5a8 8 0 0 0 3.5 3.5L16 14l4 1v3a2 2 0 0 1-2 2A12 12 0 0 1 7 9a2 2 0 0 1 2-2z" fill="#fff"/></svg>
    <ul>
      <li>No more holding or busy signal</li>
      <li>Free-up your phone line at peak periods, never miss another order</li>
      <li>Save staff time by accepting unlimited mobile and on-line orders simultaneously</li>
      <li>Send promotions to your customers of seasonal opening times or message them each time they are close to your business</li>
      <li>Differentiate your business against other local businesses</li>
      <li>Benefit from better Zintaro search results</li>
    </ul>
  </section>

  <section class="benefit-group group-right-a">
    <svg class="icon" viewBox="0 0 26 26" aria-hidden="true"><circle cx="9" cy="9" r="4" fill="var(--accent)"/><circle cx="18" cy="9" r="4" fill="var(--accent)"/><path d="M2 22a7 7 0 0 1 14 0zM11 22a7 7 0 0 1 14 0z" fill="var(--accent)"/></svg>
    <ul>
      <li>Order history is saved making re-ordering fast and convenient</li>
      <li>Use convenient online payment like KOINRA, traditional credit cards or cash on collection</li>
      <li>Launch an in-app loyalty programme</li>
      <li>We don’t encourage your customer to use a shared app that then promotes your competitors’ businesses to your customers</li>
    </ul>
  </section>

  <section class="benefit-group group-right-b">
    <svg class="icon" viewBox="0 0 26 26" aria-hidden="true"><circle cx="13" cy="13" r="12" fill="var(--accent)"/><text x="13" y="18.5" text-anchor="middle" font-family="Open Sans, sans-serif" font-weight="700" font-size="15" fill="#fff">£</text></svg>
    <ul>
      <li>We don’t charge order commission. As you grow you keep all the profits!</li>
      <li>We will also provide you an online shop that can be added to your website! (Business or Business Plus package)</li>
      <li>If you’re thinking this isn’t going to be cheap, check our pricing on our web site</li>
    </ul>
  </section>

  <div class="contact-band">
    <p>Please call us on 01632 960417 or email us at Info@Tappora-demo.com</p>
    <p>to discuss your requirements with us</p>
  </div>

  <div class="brand"><span>Tappora</span><span class="brand-mark"></span></div>
</div>
</body>
</html>
```